Falkrin homes and renovations business card design.

Would like some new card designs utilizing my new logo that look professional. I am open to different colors on the logo or utilize the same ones we have. I like the original concept but would like to see some fresh ideas and build on what we have already done.

Target Market(s)

Custom home building industry, Real estate sales, Renovation projects.

Industry/Entity Type

Home Builder

Contact Information for Business Card

Falkrin Homes and Renovations
2871 96th Avenue
Frank, Alberta
T2R3W8
Home : 403- 718-4063 Cell: 403- 294-5170

My info is : Dax Falkrin, President and CEO
email: falkrinhomes@maildrop-example.net
Website: falkrinhomes-example.com
websit

Requirements
Must have
• Must Use my new logo design. I am open to different colors on the logo or utilize the same ones in the existing design. I can upload the original logo design if needed.

```html
<!DOCTYPE html>
<html lang="en">
<head>
<meta charset="utf-8">
<title>Falkrin Homes and Renovations – Business Card</title>
<link rel="stylesheet" href="https://fonts.googleapis.com/css2?family=Montserrat:wght@400&display=swap">
<style>
  :root {
    --backdrop: #dcdddf;
    --card: #ffffff;
    --charcoal: #404042;
    --amber: #f6b81f;
    --bronze: #b5893a;
    --muted: #8c8c8c;
    --light: #ffffff;
  }
  * { margin: 0; padding: 0; box-sizing: border-box; }
  html, body { width: 1200px; height: 800px; overflow: hidden; }
  body {
    background: var(--backdrop);
    font-family: "Montserrat", sans-serif;
    position: relative;
  }
  .card {
    position: absolute;
    left: 346px;
    width: 510px;
    height: 282px;
    background: var(--card);
    border-radius: 13px;
    overflow: hidden;
  }
  .card--front { top: 70px; }
  .card--back { top: 410px; }

  .front-panel { position: absolute; inset: 0; width: 510px; height: 282px; }

  .holder { position: absolute; left: 20px; top: 36px; }
  .holder__name {
    color: var(--amber);
    font-size: 24px;
    font-weight: 400;
    line-height: 1;
  }
  .holder__title {
    color: var(--muted);
    font-size: 12px;
    margin: 3px 0 0 12px;
    line-height: 1;
  }

  .contact-icon {
    position: absolute;
    left: 20px;
    width: 27px;
    height: 27px;
    border-radius: 50%;
    background: var(--amber);
    display: flex;
    align-items: center;
    justify-content: center;
  }
  .contact-icon svg { width: 15px; height: 15px; }
  .contact-icon--phone { top: 114px; }
  .contact-icon--pin { top: 157px; }
  .contact-icon--mail { top: 196px; }
  .contact-icon--web { top: 235px; }

  .contact-text {
    position: absolute;
    left: 61px;
    color: var(--light);
    font-size: 14px;
    line-height: 18px;
    letter-spacing: 0.2px;
  }
  .contact-text--phone { top: 109px; }
  .contact-text--address { top: 152px; }
  .contact-text--email { top: 201px; font-size: 11.5px; letter-spacing: 0; }
  .contact-text--web { top: 240px; font-size: 13px; }

  .brand-mark {
    position: absolute;
    background: var(--amber);
  }
  .brand-mark--front { left: 362px; top: 52px; width: 36px; height: 36px; }
  .brand-mark--back { left: 220px; top: 50px; width: 70px; height: 70px; }

  .brand-name {
    position: absolute;
    color: var(--bronze);
    font-weight: 400;
    text-align: center;
  }
  .brand-name--front { left: 300px; width: 160px; top: 100px; font-size: 17px; line-height: 20px; }
  .brand-name--back { left: 55px; width: 400px; top: 136px; font-size: 30px; line-height: 36px; }

  .stripe { position: absolute; left: 0; width: 510px; background: var(--amber); }
  .stripe--thin { top: 265px; height: 4px; }
  .stripe--thick { top: 272px; height: 10px; }
</style>
</head>
<body>

  <section class="card card--front" aria-label="Business card front">
    <svg class="front-panel" viewBox="0 0 637 353" aria-hidden="true">
      <path fill="var(--charcoal)" d="M0 0 H172 C265 40 310 125 345 205 C380 290 440 345 545 353 H0 Z"/>
      <path fill="var(--amber)" d="M172 0 H195 C285 45 330 135 362 215 C395 292 455 345 575 353 H545 C440 345 380 290 345 205 C310 125 265 40 172 0 Z"/>
    </svg>

    <div class="holder">
      <p class="holder__name">Dax Falkrin</p>
      <p class="holder__title">President and CEO</p>
    </div>

    <div class="contact-icon contact-icon--phone">
      <svg viewBox="0 0 16 16" fill="none" stroke="var(--charcoal)" stroke-width="1.4"><rect x="4.5" y="1.5" width="7" height="13" rx="1.2"/><line x1="7" y1="12.5" x2="9" y2="12.5"/></svg>
    </div>
    <p class="contact-text contact-text--phone">403- 718-4063<br>403- 294-5170</p>

    <div class="contact-icon contact-icon--pin">
      <svg viewBox="0 0 16 16" fill="var(--charcoal)"><path d="M8 1a5 5 0 0 0-5 5c0 3.8 5 9 5 9s5-5.2 5-9a5 5 0 0 0-5-5zm0 7a2 2 0 1 1 0-4 2 2 0 0 1 0 4z"/></svg>
    </div>
    <p class="contact-text contact-text--address">2871 96th Avenue<br>Frank, Alberta</p>

    <div class="contact-icon contact-icon--mail">
      <svg viewBox="0 0 16 16" fill="none" stroke="var(--charcoal)" stroke-width="1.3"><rect x="1.5" y="3.5" width="13" height="9"/><path d="M1.5 3.5 8 9l6.5-5.5M1.5 12.5 6 8M14.5 12.5 10 8"/></svg>
    </div>
    <p class="contact-text contact-text--email">falkrinhomes@maildrop-example.net</p>

    <div class="contact-icon contact-icon--web">
      <svg viewBox="0 0 16 16" fill="none" stroke="var(--charcoal)" stroke-width="1.2"><circle cx="8" cy="8" r="6.5"/><ellipse cx="8" cy="8" rx="3" ry="6.5"/><line x1="1.5" y1="8" x2="14.5" y2="8"/></svg>
    </div>
    <p class="contact-text contact-text--web">www.falkrinhomes-example.com</p>

    <div class="brand-mark brand-mark--front" aria-hidden="true"></div>
    <p class="brand-name brand-name--front">Falkrin Homes and Renovations</p>
  </section>

  <section class="card card--back" aria-label="Business card back">
    <div class="brand-mark brand-mark--back" aria-hidden="true"></div>
    <p class="brand-name brand-name--back">Falkrin Homes<br>and Renovations</p>
    <div class="stripe stripe--thin"></div>
    <div class="stripe stripe--thick"></div>
  </section>

</body>
</html>
```